Calden L - Premium Business Cards

Background of Calden L
Calden Leafworks is a cigar mobile lounge where guests become family. A place of luxury, relaxation, and ambiance is the global popularity demand. Calden Leafworks strives to provide first-class service of quality and products. Our goal is to ensure that every guest is treated and serviced as a VIP.

Calden Leafworks was founded by Dennis Markow Jr in January 2020. After 15 years of cigar reviews and research Dennis decided it was time to launch his own cigar brand and boutique cigar company. With a wealth of knowledge and years of experience Calden Leafworks was born. With opulence for all cultures, Calden Leafworks offers hand rolled cigars with premium blend tobacco from sweet to bold imported from Costa Rica, Dominican Republic, and Nicaragua. Thank you for your business!

Objective:
Create a business card template to be used for all employees. Design should communicate premium and classy. And should use earth tone colors.

Design should include:
1. Client wants to incorporate the cigar leaf
2. Logo
3. Tagline: Respect the smoke
3. Content info:
Kevin Oldacre
Owner
555-017-4863
koldacre@caldenleaf.com
caldenleafworks.com

```html
<!DOCTYPE html>
<html lang="en">
<head>
<meta charset="utf-8">
<title>Calden Leafworks – Business Card</title>
<link rel="stylesheet" href="https://fonts.googleapis.com/css2?family=Bebas+Neue&family=Lato:wght@400;700&display=swap">
<style>
  :root {
    --backdrop: #202020;
    --card: #111111;
    --band: #e8e6e8;
    --ink: #ffffff;
    --ink-soft: #d9d9d9;
    --rule: #8a8a8a;
  }
  * { margin: 0; padding: 0; box-sizing: border-box; }
  html, body {
    width: 1200px; height: 900px; overflow: hidden;
    background: var(--backdrop);
  }
  .stage {
    width: 1200px; height: 900px;
    display: flex; flex-direction: column; align-items: center; justify-content: center;
    gap: 40px;
  }
  .card {
    position: relative;
    width: 640px; height: 360px;
    background: var(--card);
    box-shadow: 0 10px 30px rgba(0,0,0,.55);
    overflow: hidden;
  }
  .card-band {
    position: absolute; left: 0; right: 0; bottom: 0;
    height: 16px; background: var(--band);
  }
  /* Front */
  .card-front {
    display: flex; flex-direction: column; align-items: center; justify-content: center;
    padding-bottom: 16px;
  }
  .brand-name {
    font-family: "Lato", sans-serif; font-weight: 700;
    font-size: 54px; color: var(--ink);
    letter-spacing: 1px;
  }
  .tagline {
    margin-top: 28px;
    font-family: "Lato", sans-serif; font-weight: 700;
    font-size: 21px; color: var(--ink);
    text-transform: uppercase; letter-spacing: 0.5px;
  }
  /* Back */
  .card-back {
    display: flex; align-items: center;
    padding: 0 0 16px 0;
  }
  .person {
    width: 300px; text-align: right; padding-right: 28px;
    margin-top: -40px;
  }
  .person-name {
    font-family: "Bebas Neue", sans-serif;
    font-size: 40px; line-height: 1; color: var(--ink-soft);
    letter-spacing: 0.5px;
  }
  .person-role {
    font-family: "Lato", sans-serif; font-size: 17px;
    color: var(--ink-soft); margin-top: 4px;
  }
  .divider {
    width: 1px; height: 96px; background: var(--rule);
  }
  .contact-list {
    list-style: none; padding-left: 26px;
    font-family: "Lato", sans-serif; font-size: 18px; color: var(--ink);
  }
  .contact-list li {
    display: flex; align-items: center; gap: 10px; line-height: 1.5;
  }
  .contact-icon { width: 18px; height: 18px; flex: none; }
</style>
</head>
<body>
<main class="stage">
  <section class="card card-front">
    <p class="brand-name">Calden Leafworks</p>
    <p class="tagline">Respect the smoke</p>
    <div class="card-band"></div>
  </section>

  <section class="card card-back">
    <div class="person">
      <p class="person-name">KEVIN OLDACRE</p>
      <p class="person-role">Owner</p>
    </div>
    <div class="divider"></div>
    <ul class="contact-list">
      <li>
        <svg class="contact-icon" viewBox="0 0 24 24" fill="none" stroke="#fff" stroke-width="2" stroke-linecap="round" stroke-linejoin="round"><path d="M5 3h4l2 5-3 2a11 11 0 0 0 6 6l2-3 5 2v4a2 2 0 0 1-2 2A17 17 0 0 1 3 5a2 2 0 0 1 2-2z"/></svg>
        555-017-4863
      </li>
      <li>
        <svg class="contact-icon" viewBox="0 0 24 24" fill="none" stroke="#fff" stroke-width="2" stroke-linejoin="round"><rect x="2" y="5" width="20" height="14"/><path d="M2 5l10 8 10-8"/></svg>
        koldacre@caldenleaf.com
      </li>
      <li>
        <svg class="contact-icon" viewBox="0 0 24 24" fill="none" stroke="#fff" stroke-width="2"><circle cx="12" cy="12" r="10"/><ellipse cx="12" cy="12" rx="4" ry="10"/><path d="M2 12h20M4 7h16M4 17h16"/></svg>
        caldenleafworks.com
      </li>
    </ul>
    <div class="card-band"></div>
  </section>
</main>
</body>
</html>
```